Hair, nails, face pamper parties

Name - Silver Lantern's
Product - Bluebell Dazzle Days
For Girls 5 to 15
Colourful pictures or cartoon style images showing hair, face and fingers
Customers will get hair styling, finger & toe nail designs, glitter stick-on tattoos, face painting
Work by qualified beautician & nail technician and qualified hairdresser

```html
<!DOCTYPE html>
<html lang="en">
<head>
<meta charset="utf-8">
<title>Silver Lantern's Bluebell Dazzle Days – Flyer</title>
<link rel="stylesheet" href="https://fonts.googleapis.com/css2?family=Raleway:wght@500;700;800&family=Cabin:wght@500;600;700&family=Great+Vibes&display=swap">
<style>
  :root {
    --page: #ffffff;
    --plum-deep: #3a0f33;
    --plum: #5e1d52;
    --plum-light: #8a3a7a;
    --pink: #d4478f;
    --pink-band: #c94583;
    --pink-soft: rgba(214, 92, 160, 0.35);
    --white: #ffffff;
    --ring: #e05aa0;
  }
  * { box-sizing: border-box; margin: 0; padding: 0; }
  html, body { width: 1200px; height: 849px; overflow: hidden; background: var(--page); }
  .sheet { position: relative; width: 1200px; height: 849px; }

  .flyer {
    position: absolute; top: 43px; width: 539px; height: 765px; overflow: hidden;
    background:
      radial-gradient(ellipse at 35% 30%, var(--plum-light) 0%, transparent 55%),
      radial-gradient(ellipse at 70% 75%, var(--plum-light) 0%, transparent 50%),
      linear-gradient(160deg, var(--plum) 0%, var(--plum-deep) 100%);
    color: var(--white);
  }
  .flyer--front { left: 53px; }
  .flyer--back { left: 608px; }
  .flyer__band { position: absolute; left: 0; right: 0; bottom: 0; height: 31px; background: var(--pink-band); }

  .brand-plaque {
    position: absolute; background: var(--white); border: 5px solid var(--pink);
    border-radius: 40px;
    display: flex; align-items: center; justify-content: center; text-align: center;
  }
  .brand-plaque__name {
    font-family: "Raleway", sans-serif; font-weight: 700; color: var(--pink);
    font-size: 31px; line-height: 1.25; letter-spacing: 0.5px;
  }
  .flyer--front .brand-plaque { left: 22px; top: 42px; width: 320px; height: 330px; }
  .flyer--back .brand-plaque { left: 95px; top: 65px; width: 345px; height: 345px; }

  .photo-portrait {
    position: absolute; left: 250px; top: 154px; width: 289px; height: 580px;
    background: linear-gradient(180deg, #c98a70 0%, #e7c2b0 30%, #f2d8dc 60%, #e0a0a8 100%);
    border-radius: 120px 0 0 0; opacity: 0.9;
  }

  .features {
    position: absolute; left: 62px; top: 384px; width: 231px; height: 276px;
    background: var(--pink-soft);
    font-family: "Raleway", sans-serif; font-weight: 500; font-size: 17.5px;
    line-height: 1.2; text-align: center; letter-spacing: 0.3px;
    display: flex; flex-direction: column; justify-content: center; gap: 12px;
  }
  .price {
    position: absolute; left: 62px; top: 677px; width: 231px; text-align: center;
    font-family: "Cabin", sans-serif; font-weight: 700; font-size: 23px; letter-spacing: 0.5px;
  }

  .ring { position: absolute; border: 3px solid var(--ring); border-radius: 50%; }
  .photo-circle { position: absolute; border: 5px solid var(--ring); border-radius: 50%; }
  .photo-circle--face { left: -4px; top: 5px; width: 136px; height: 136px; background: linear-gradient(135deg, #f0c9b8, #e9a07a 60%, #b7d4e8); }
  .photo-circle--nails { left: 394px; top: 0px; width: 146px; height: 146px; background: linear-gradient(135deg, #f4b5c0, #e88a9c 60%, #f6d4d8); }
  .photo-circle--group { left: -12px; top: 273px; width: 136px; height: 136px; background: linear-gradient(135deg, #e7b8b0, #f3d2cc 50%, #d7584d); }
  .photo-circle--play { left: 430px; top: 246px; width: 128px; height: 128px; background: linear-gradient(135deg, #f1c84a, #e96a4a 50%, #f4eef0); }

  .line { position: absolute; left: 0; width: 530px; text-align: center; white-space: nowrap; }
  .contact__name { font-family: "Cabin", sans-serif; font-weight: 600; font-size: 21px; line-height: 1; }
  .contact__role { font-family: "Raleway", sans-serif; font-weight: 700; font-size: 12px; letter-spacing: 0.4px; line-height: 1.3; }
  .contact__phone { font-family: "Cabin", sans-serif; font-weight: 500; font-size: 20px; letter-spacing: 0.5px; line-height: 1; }
  .tagline { font-family: "Great Vibes", cursive; font-size: 54px; line-height: 1; }
  .note { font-family: "Raleway", sans-serif; font-weight: 700; font-size: 12px; letter-spacing: 0.5px; line-height: 1; }
  .detail { font-family: "Cabin", sans-serif; font-weight: 500; font-size: 17px; line-height: 1; }
  .social-square { position: absolute; left: 365px; top: 680px; width: 38px; height: 38px; background: var(--white); border-radius: 4px; }
</style>
</head>
<body>
<div class="sheet">

  <section class="flyer flyer--front">
    <div class="photo-portrait" role="img" aria-label="Photo of a young girl in a floral dress looking up"></div>
    <div class="brand-plaque">
      <p class="brand-plaque__name">Silver Lantern's<br>Bluebell Dazzle Days</p>
    </div>
    <div class="features">
      <p>★ CHOICE OF<br>HAIR STYLES</p>
      <p>★ FINGER/ TOES<br>SELECTION</p>
      <p>★ STICK-ON<br>GLITTER TATTOOS</p>
      <p>★ FACE PAINTING</p>
      <p>★ PRINCESS<br>GOODY BAGS</p>
    </div>
    <p class="price">£10 PER CHILD</p>
    <div class="flyer__band"></div>
  </section>

  <section class="flyer flyer--back">
    <div class="ring" style="left:20px;top:150px;width:100px;height:100px;"></div>
    <div class="ring" style="left:430px;top:150px;width:110px;height:110px;"></div>
    <div class="ring" style="left:0px;top:230px;width:70px;height:70px;"></div>
    <div class="ring" style="left:410px;top:330px;width:90px;height:90px;"></div>
    <div class="ring" style="left:150px;top:-40px;width:90px;height:90px;"></div>
    <div class="ring" style="left:330px;top:-20px;width:70px;height:70px;"></div>

    <div class="photo-circle photo-circle--face" role="img" aria-label="Photo of a girl having her face painted"></div>
    <div class="photo-circle photo-circle--nails" role="img" aria-label="Photo of fingernails being painted"></div>
    <div class="photo-circle photo-circle--group" role="img" aria-label="Photo of girls at a party wearing tiaras"></div>
    <div class="photo-circle photo-circle--play" role="img" aria-label="Photo of a girl in a ball pit"></div>

    <div class="brand-plaque">
      <p class="brand-plaque__name">Silver Lantern's<br>Bluebell Dazzle Days</p>
    </div>

    <p class="line contact__name" style="top:452px;">Dana Whitfield</p>
    <p class="line contact__role" style="top:475px;">QUALIFIED BEAUTICIAN<br>&amp; NAIL TECHNICIAN</p>
    <p class="line contact__phone" style="top:510px;">07700 900412</p>
    <p class="line contact__name" style="top:540px;">Rosa Pennington</p>
    <p class="line contact__role" style="top:563px;">QUALIFIED HAIRDRESSER</p>
    <p class="line contact__phone" style="top:586px;">07700 900738</p>
    <p class="line tagline" style="top:612px;">We can come to you</p>
    <p class="line note" style="top:660px;">WILL TAKE 2 TO 3 HOURS</p>
    <p class="line detail" style="top:680px;">Age range 5-15</p>
    <p class="line detail" style="top:704px;left:-40px;">Visit our Friendbook page</p>
    <div class="social-square"></div>
    <div class="flyer__band"></div>
  </section>

</div>
</body>
</html>
```